Facial Tissue Brand Logo and Design

We would like you to design a Logo for the Facial Tissue Brand "Velora" along with the box design. The pack should indicate the pack size (150 x 2 ply). Also our company logo should be present (attached) along with a barcode. The box size dimensions should be 210mm (L) x 110mm (W) x 70mm (H). We are open to all kinds of nice designs which are attractive but not overdone. Happy designing!

UPDATE:
We appreciate the designs so far... but would also love to see more options in a simple and elegent design style that would look good on a table... please see attached below links for reference purpose:

www.pictovault-example.com/image-photo/cleaning-wipes-isolated-on-white-257770819

www.pictovault-example.com/image-photo/cleaning-wipes-isolated-on-white-155326937

www.pictovault-example.com/image-photo/delicate-female-hands-pulling-tissue-out-1330426586

Happy desgining!

We appreciate the designs so far.. but would like to to see some more options.

```html
<!DOCTYPE html>
<html lang="en">
<head>
<meta charset="utf-8">
<title>Velora Facial Tissues – Box Artwork</title>
<link href="https://fonts.googleapis.com/css2?family=Kaushan+Script&family=Montserrat:wght@400;600;800&display=swap" rel="stylesheet">
<style>
  :root {
    --bg: #ececee;
    --blue-deep: #143f6e;
    --blue-mid: #23659c;
    --blue-light: #3a8fd0;
    --blue-accent: #2f7fd6;
    --white: #ffffff;
    --pattern-a: #fbf3f1;
    --pattern-b: #f1dcd7;
    --grey-text: #8a93a6;
    --sans: "Montserrat", Arial, sans-serif;
    --script: "Kaushan Script", cursive;
  }
  * { box-sizing: border-box; margin: 0; padding: 0; }
  html, body { width: 1200px; height: 750px; overflow: hidden; background: var(--bg); }
  .artwork { position: absolute; left: 100px; top: 50px; width: 1000px; height: 650px; box-shadow: 0 10px 30px rgba(0,0,0,.15); }
  .panel { position: absolute; overflow: hidden; color: var(--white); font-family: var(--sans); }

  .panel--end { left: 0; top: 0; width: 180px; height: 650px; background: var(--white); border-right: 1px solid rgba(0,0,0,.08); }
  .panel--top { left: 180px; top: 0; width: 820px; height: 400px; background: radial-gradient(ellipse at 30% 30%, var(--blue-light) 0%, var(--blue-mid) 45%, var(--blue-deep) 100%); }
  .panel--front { left: 180px; top: 400px; width: 820px; height: 250px; background: linear-gradient(180deg, var(--blue-mid) 0%, var(--blue-deep) 100%); border-top: 1px solid rgba(255,255,255,.15); }

  .layer { position: absolute; inset: 0; }
  .pack-count { position: absolute; text-align: center; line-height: 1; }
  .pack-count__num { font-size: 24px; font-weight: 400; letter-spacing: 1px; }
  .pack-count__unit { display: block; font-size: 10px; font-weight: 600; letter-spacing: 1px; text-transform: uppercase; }
  .ply-icon { position: absolute; width: 50px; height: 30px; }
  .product-type { position: absolute; font-size: 10px; font-weight: 600; line-height: 1.2; text-transform: uppercase; letter-spacing: .3px; }
  .brand { position: absolute; font-family: var(--sans); font-weight: 800; color: var(--white); letter-spacing: 1px; line-height: 1; }
  .tagline { position: absolute; font-family: var(--script); color: var(--white); line-height: 1; white-space: nowrap; }
  .sheet-size { position: absolute; font-size: 13px; font-weight: 400; letter-spacing: .3px; white-space: nowrap; }

  .maker { position: absolute; left: 14px; bottom: 30px; display: flex; align-items: center; gap: 6px; }
  .maker__mark { width: 12px; height: 12px; background: var(--blue-mid); }
  .maker__name { font-size: 10px; font-weight: 600; color: var(--blue-mid); letter-spacing: .5px; text-transform: uppercase; white-space: nowrap; }
  .maker__place { position: absolute; left: 14px; bottom: 14px; font-size: 7px; color: var(--grey-text); letter-spacing: 2.5px; text-transform: uppercase; white-space: nowrap; }
</style>
</head>
<body>
<main class="artwork">

  <section class="panel panel--end">
    <svg class="layer" viewBox="0 0 180 650" role="img" aria-label="Floral pattern of red and grey flowers and leaves on white">
      <defs>
        <linearGradient id="endTone" x1="0" y1="0" x2="1" y2="1">
          <stop offset="0" stop-color="var(--pattern-a)"/>
          <stop offset="1" stop-color="var(--pattern-b)"/>
        </linearGradient>
      </defs>
      <rect x="0" y="0" width="180" height="585" fill="url(#endTone)"/>
    </svg>
    <div class="maker">
      <span class="maker__mark"></span>
      <span class="maker__name">Norvane Trading FZC</span>
    </div>
    <span class="maker__place">United Arab Emirates</span>
  </section>

  <section class="panel panel--top">
    <svg class="layer" viewBox="0 0 820 400" role="img" aria-label="Floral pattern of red and navy flowers, leaves and sprigs on white">
      <defs>
        <linearGradient id="patternTone" x1="0" y1="0" x2="1" y2="1">
          <stop offset="0" stop-color="var(--pattern-a)"/>
          <stop offset="1" stop-color="var(--pattern-b)"/>
        </linearGradient>
      </defs>
      <path d="M570,0 C520,180 550,330 750,400 L820,400 L820,0 Z" fill="url(#patternTone)"/>
    </svg>
    <svg class="layer" viewBox="0 0 820 400" aria-hidden="true">
      <path d="M570,0 C520,180 550,330 750,400" fill="none" stroke="var(--blue-accent)" stroke-width="10"/>
    </svg>

    <div class="pack-count" style="left:28px; top:32px;">
      <span class="pack-count__num">150</span>
      <span class="pack-count__unit">Pulls</span>
    </div>
    <svg class="ply-icon" style="left:96px; top:30px;" viewBox="0 0 50 30" aria-label="2 ply">
      <path d="M4,18 L40,18 L46,12" fill="none" stroke="var(--white)" stroke-width="2"/>
      <path d="M4,24 L40,24 L46,18" fill="none" stroke="var(--white)" stroke-width="2"/>
      <text x="22" y="13" fill="var(--white)" font-family="Montserrat, sans-serif" font-size="13" font-weight="600">2</text>
    </svg>
    <p class="product-type" style="left:170px; top:38px;">Non-lotion white facial tissue<br>Mouchoirs blancs sans lotion</p>

    <h1 class="brand" style="left:50px; top:100px; font-size:96px;">Velora</h1>
    <p class="tagline" style="left:70px; top:228px; font-size:38px;">Soft White</p>
    <p class="tagline" style="left:290px; top:234px; font-size:28px;">Facial Tissues</p>
    <p class="sheet-size" style="left:50px; top:340px;">21.3cm X 20.8cm (8.4 IN/PO X 8.2 IN/PO)</p>
  </section>

  <section class="panel panel--front">
    <svg class="layer" viewBox="0 0 820 250" aria-hidden="true">
      <path d="M0,150 C60,150 110,175 170,210 C215,236 250,250 290,250 L0,250 Z" fill="var(--white)"/>
    </svg>

    <div class="pack-count" style="right:116px; top:24px;">
      <span class="pack-count__num">150</span>
      <span class="pack-count__unit">Pulls</span>
    </div>
    <svg class="ply-icon" style="right:40px; top:22px;" viewBox="0 0 50 30" aria-label="2 ply">
      <path d="M4,18 L40,18 L46,12" fill="none" stroke="var(--white)" stroke-width="2"/>
      <path d="M4,24 L40,24 L46,18" fill="none" stroke="var(--white)" stroke-width="2"/>
      <text x="22" y="13" fill="var(--white)" font-family="Montserrat, sans-serif" font-size="13" font-weight="600">2</text>
    </svg>

    <p class="brand" style="left:350px; top:56px; font-size:72px;">Velora</p>
    <p class="tagline" style="left:370px; top:144px; font-size:28px;">Soft White</p>
    <p class="tagline" style="left:540px; top:148px; font-size:22px;">Facial Tissues</p>
    <p class="sheet-size" style="right:26px; bottom:20px; font-size:12px;">21.3cm X 20.8cm (8.4 IN/PO X 8.2 IN/PO)</p>
  </section>

</main>
</body>
</html>
```